Stayvora.com banner design

Stayvora.com is looking for a designer to work with ongoing to create a variety of banners.

For this competition we are looking for entrants to create two flash banners with dimensions 300x250 and a static banner/jpg. Each flash banner has two separate concepts one with more copy and more required 'slides' and one with less. The copy for each banner is as follows:

Concept 1: - 4 slide flash banner/animated gif
Save up to 75% on 150,000 Hotels Worldwide.
10% of profits go to local charities.
Do something good when you travel.
End screen call to action - Book now @ stayvora.com (click here)

Concept 1a: 3 slide flash banner/animated gif

Concept 2: 4 slide flash banner/animated gif
$0 Booking fees. Best price guarantee.

Concept 2a: 3 slide flash banner/animated gif

Concept 3 – Static Banner
Book now @ stayvora.com (click here)

Concept 3a

We expect two different designs, one for Concept 1 and 1a and a different design for concept 2 and 2a. Concept 3 (the static banners) can adopt the design used for the flash banners.

We also expect a gif version of the flash banners to be delivered.

The winning entry will then be hired to create each banner in a variety of banner sizes.

Reason: We are not satisfied with the number of entries so are extending this competition. We are looking for a long term relationship with a quality designer to produce a whole range of banners and other designs for stayvora.com.

Industry/Entity Type

Accommodation

Requirements
Must have
• The stayvora.com logo must always be visible on all banners.

Maximum flash file size is 50k
Max Frame Rate 24fps

```html
<!DOCTYPE html>
<html lang="en">
<head>
<meta charset="utf-8">
<title>Stayvora.com banner concepts</title>
<link href="https://fonts.googleapis.com/css2?family=Source+Sans+3:wght@600;700;800&display=swap" rel="stylesheet">
<style>
  :root{
    --page:#ffffff;
    --heading:#3a3a3a;
    --frame:#6e6e6e;
    --orange:#f0961c;
    --orange-dark:#d97f0c;
    --tile-grey-top:#8a8a8a;
    --tile-grey-bottom:#555555;
    --ink:#111111;
    --white:#ffffff;
    --button-top:#3cc3ee;
    --button-bottom:#1591c8;
    --label-band:rgba(40,30,20,0.72);
    --brand:#ffffff;
    --brand-dot:#f0961c;
  }
  *{box-sizing:border-box;margin:0;padding:0}
  html,body{width:1200px;height:1000px;overflow:hidden;background:var(--page)}
  body{position:relative;font-family:"Source Sans 3",Arial,sans-serif}
  .page-title{position:absolute;top:161px;left:0;width:1200px;text-align:center;font-size:22px;font-weight:700;color:var(--heading);letter-spacing:0.2px}
  .banner{position:absolute;width:300px;height:250px;background:var(--frame)}
  .tile{position:absolute;width:146px;height:120px;border-radius:5px;overflow:hidden;box-shadow:1px 2px 2px rgba(0,0,0,0.45)}
  .tile.left{left:3px}.tile.right{left:151px}
  .tile.top{top:3px}.tile.bottom{top:126px}
  .photo-rome{background:linear-gradient(180deg,#1d4fc9 0%,#2c3f9a 35%,#8a4a22 60%,#5a2a14 100%)}
  .photo-bangkok{background:linear-gradient(180deg,#8fb7e0 0%,#c8a55a 35%,#a57a30 70%,#6e4b1c 100%)}
  .photo-cancun{background:linear-gradient(160deg,#7fd3cf 0%,#5cc7c4 40%,#bfe3d8 60%,#e8cfa4 80%,#d8b07a 100%)}
  .place-label{position:absolute;left:10px;right:-6px;bottom:10px;height:22px;background:var(--label-band);transform:skewX(-20deg)}
  .place-name{position:absolute;left:0;right:0;bottom:10px;height:22px;line-height:22px;text-align:center;color:var(--white);font-weight:700;font-size:19px}
  .promo{background:linear-gradient(180deg,#f6a125,var(--orange-dark));color:var(--white);font-weight:800;text-align:center;text-shadow:0 1px 1px rgba(0,0,0,0.25)}
  .promo .line{display:block;line-height:1}
  .promo.save{text-align:left;padding:7px 0 0 8px}
  .save .big{font-size:54px;line-height:0.88;letter-spacing:0.5px}
  .save .small{font-size:19px;line-height:1.02;margin-top:0}
  .save .big + .small{margin-top:4px}
  .charity{padding-top:6px}
  .charity .big{font-size:52px;line-height:0.86}
  .charity .mid{font-size:22px;line-height:1;margin-top:4px}
  .charity .small{font-size:18px;line-height:1.05;font-weight:700}
  .good{padding-top:6px}
  .good .s{font-size:17px;line-height:1.05}
  .good .b{font-size:38px;line-height:0.9}
  .good .m{font-size:17px;line-height:1.05}
  .book{background:linear-gradient(180deg,var(--tile-grey-top),var(--tile-grey-bottom));text-align:center}
  .book-line{position:absolute;top:14px;left:0;right:0;font-size:21px;font-weight:700;color:var(--ink)}
  .book-line .at{font-size:17px}
  .brand{position:absolute;top:50px;left:0;right:0;display:flex;align-items:center;justify-content:center;gap:5px;color:var(--brand);font-size:15px;font-weight:700}
  .brand-dot{width:12px;height:12px;border-radius:50%;background:var(--brand-dot)}
  .cta{position:absolute;top:83px;left:22px;width:104px;height:25px;border-radius:4px;background:linear-gradient(180deg,var(--button-top),var(--button-bottom));color:var(--white);font-size:15px;font-weight:700;line-height:25px;box-shadow:1px 2px 2px rgba(0,0,0,0.4)}
</style>
</head>
<body>
  <h1 class="page-title">Auto image flip rotation animation and on user rollOver also</h1>

  <!-- Frame 1 -->
  <section class="banner" style="left:203px;top:212px">
    <div class="tile left top photo-rome" role="img" aria-label="Photo of the Colosseum in Rome at dusk"><span class="place-label"></span><span class="place-name">Rome</span></div>
    <div class="tile right top photo-bangkok" role="img" aria-label="Photo of a golden temple in Bangkok"><span class="place-label"></span><span class="place-name">Bangkok</span></div>
    <div class="tile left bottom photo-cancun" role="img" aria-label="Photo of a turquoise beach in Cancun"><span class="place-label"></span><span class="place-name">Cancun</span></div>
    <div class="tile right bottom book"><p class="book-line">Book Now <span class="at">@</span></p><div class="brand"><span class="brand-dot"></span>Stayvora.com</div><div class="cta">CLICK HERE</div></div>
  </section>

  <!-- Frame 2 -->
  <section class="banner" style="left:676px;top:212px">
    <div class="tile left top promo save"><span class="line big">SAVE</span><span class="line small">up to 75% on</span><span class="line small">150,000 Hotels</span><span class="line small">Worldwide</span></div>
    <div class="tile right top photo-bangkok" role="img" aria-label="Photo of a golden temple in Bangkok"><span class="place-label"></span><span class="place-name">Bangkok</span></div>
    <div class="tile left bottom photo-cancun" role="img" aria-label="Photo of a turquoise beach in Cancun"><span class="place-label"></span><span class="place-name">Cancun</span></div>
    <div class="tile right bottom book"><p class="book-line">Book Now <span class="at">@</span></p><div class="brand"><span class="brand-dot"></span>Stayvora.com</div><div class="cta">CLICK HERE</div></div>
  </section>

  <!-- Frame 3 -->
  <section class="banner" style="left:203px;top:514px">
    <div class="tile left top photo-rome" role="img" aria-label="Photo of the Colosseum in Rome at dusk"><span class="place-label"></span><span class="place-name">Rome</span></div>
    <div class="tile right top promo charity"><span class="line big">10%</span><span class="line mid">OF PROFITS</span><span class="line small">go to</span><span class="line small">local charities</span></div>
    <div class="tile left bottom photo-cancun" role="img" aria-label="Photo of a turquoise beach in Cancun"><span class="place-label"></span><span class="place-name">Cancun</span></div>
    <div class="tile right bottom book"><p class="book-line">Book Now <span class="at">@</span></p><div class="brand"><span class="brand-dot"></span>Stayvora.com</div><div class="cta">CLICK HERE</div></div>
  </section>

  <!-- Frame 4 -->
  <section class="banner" style="left:676px;top:514px">
    <div class="tile left top photo-rome" role="img" aria-label="Photo of the Colosseum in Rome at dusk"><span class="place-label"></span><span class="place-name">Rome</span></div>
    <div class="tile right top photo-bangkok" role="img" aria-label="Photo of a golden temple in Bangkok"><span class="place-label"></span><span class="place-name">Bangkok</span></div>
    <div class="tile left bottom promo good"><span class="line s">DO SOMETHING</span><span class="line b">GOOD</span><span class="line m">WHEN YOU</span><span class="line b">TRAVEL</span></div>
    <div class="tile right bottom book"><p class="book-line">Book Now <span class="at">@</span></p><div class="brand"><span class="brand-dot"></span>Stayvora.com</div><div class="cta">CLICK HERE</div></div>
  </section>
</body>
</html>
```